Website for new dental office

I am Dr. Colin Ashford and am building a new dental practice. I specialize in general dentistry. I am young and have a higher end dental practice incorporating very new technologies and would like my website to reflect that. As many dental patients are older, the website must be very easy to navigate. I would like patients to be able to request appointments, and will eventually add on patient information forms (the health history, etc, that you normally fill out in the practice) from my practice management software, so leave an area for that.

Industry/Entity Type

Building

```html
<!DOCTYPE html>
<html lang="en">
<head>
<meta charset="utf-8">
<title>Ashford Dental</title>
<link href="https://fonts.googleapis.com/css2?family=Arimo:wght@400;700&family=Ubuntu:wght@400;500&display=swap" rel="stylesheet">
<style>
:root{
  --green:#0ea468;
  --green-light:#22c88a;
  --blue:#26509a;
  --link:#2a6db5;
  --ink:#222;
  --body-text:#666;
  --line:#222;
  --band:#e6e8ea;
  --footer:#000;
  --field-border:#cfcfcf;
}
*{box-sizing:border-box;margin:0;padding:0}
html,body{width:1018px;height:1200px;overflow:hidden;background:#fff}
body{position:relative;font-family:"Arimo",Arial,sans-serif;color:var(--ink)}
.abs{position:absolute}

.site-header{position:absolute;left:0;top:0;width:1018px;height:94px;background:#fff;border-bottom:1px solid #bbb}
.brand{position:absolute;left:85px;top:22px;display:flex;align-items:center;gap:10px}
.brand-dot{width:46px;height:46px;border-radius:50%;background:var(--blue)}
.brand-name{font-family:"Ubuntu",sans-serif;font-weight:500;font-size:25px;line-height:26px;color:var(--green)}
.main-nav{position:absolute;left:417px;top:44px;width:517px;height:27px;border-bottom:2px solid var(--line);font-size:12.5px}
.main-nav a{color:var(--ink);text-decoration:none;position:absolute;top:1px}
.main-nav .active::after{content:"";position:absolute;left:-19px;right:-15px;top:23px;height:2px;background:var(--green)}

.hero{position:absolute;left:0;top:94px;width:1018px;height:467px;
  background:
    radial-gradient(ellipse 190px 230px at 640px 240px,#f6f4f1 0%,rgba(246,244,241,0) 100%),
    radial-gradient(ellipse 230px 200px at 870px 330px,#e8c9a6 0%,rgba(232,201,166,0) 100%),
    radial-gradient(ellipse 170px 260px at 200px 260px,#ece8e4 0%,rgba(236,232,228,0) 100%),
    linear-gradient(100deg,#9e9890 0%,#c9bfb2 22%,#d7cbbb 45%,#c8b79f 70%,#a89074 100%)}
.appointment-btn{position:absolute;left:569px;top:464px;width:364px;height:53px;background:var(--green);color:#fff;font-family:"Ubuntu",sans-serif;font-weight:500;font-size:24px;display:flex;align-items:center;padding-left:15px;gap:12px;box-shadow:0 2px 4px rgba(0,0,0,.25)}

.patient-form{position:absolute;left:85px;top:533px;width:365px;height:264px;border-radius:5px;background:linear-gradient(#e9e9e9,#fff 40%,#dcdcdc);box-shadow:0 1px 3px rgba(0,0,0,.25)}
.patient-form h2{position:absolute;left:52px;top:22px;font-weight:400;font-size:34px;color:var(--blue)}
.field{position:absolute;height:27px;background:#fff;border:1px solid var(--field-border);font-size:11px;color:#777;padding:7px 10px}
.submit-btn{position:absolute;left:152px;top:217px;width:180px;height:30px;background:linear-gradient(var(--green-light),var(--green));color:#fff;font-weight:700;font-size:11.5px;letter-spacing:.4px;display:flex;align-items:center;justify-content:center}

.about{position:absolute;left:474px;top:582px;width:448px}
.about h2{font-weight:400;font-size:19.5px;color:#333;margin-bottom:10px}
.about p{font-size:10.6px;line-height:17px;color:var(--body-text)}
.read-more{font-size:10.6px;color:var(--link)}
.about .read-more{color:var(--link)}

.services{position:absolute;left:0;top:850px;width:1018px;height:248px;background:linear-gradient(var(--band),#f4f4f4)}
.service-photo{position:absolute;width:83px;height:83px;border-radius:50%;border:4px solid #fff;box-shadow:0 3px 6px rgba(0,0,0,.3)}
.service-plus{position:absolute;width:26px;height:26px;border-radius:50%;background:#fff;border:3px solid #aaa}
.service-text{position:absolute;width:154px;font-size:10.6px;line-height:15.3px;color:var(--body-text);text-align:center}
.skyline{position:absolute;left:352px;top:1078px;width:345px;height:20px;background:radial-gradient(ellipse 50% 100% at 50% 100%,#111 0%,#111 55%,rgba(17,17,17,0) 100%)}

.site-footer{position:absolute;left:0;top:1098px;width:1018px;height:102px;background:var(--footer)}
.footer-brand{position:absolute;left:83px;top:33px;display:flex;align-items:center;gap:7px}
.footer-brand .brand-dot{width:30px;height:30px}
.footer-brand .brand-name{font-size:16px;line-height:17px;color:#2c8fd6}
.contact{position:absolute;left:197px;top:28px;font-size:11px;line-height:18.5px;color:#bbb}
.social{position:absolute;left:436px;top:45px;display:flex;gap:11px}
.social span{width:28px;height:28px;border-radius:50%;background:radial-gradient(#eee,#999);box-shadow:0 0 0 3px #333}
.newsletter{position:absolute;left:695px;top:45px;width:235px;height:28px;background:#fff;border:1px solid #ccc;font-size:10px;color:#555;padding:8px}
</style>
</head>
<body>

<header class="site-header">
  <div class="brand"><span class="brand-dot"></span><span class="brand-name">Ashford<br>Dental</span></div>
  <nav class="main-nav">
    <a class="active" href="#" style="left:19px">Home</a>
    <a href="#" style="left:81px">Dentists Staff</a>
    <a href="#" style="left:198px">Services</a>
    <a href="#" style="left:289px">Location</a>
    <a href="#" style="left:380px">Specialist</a>
    <a href="#" style="left:477px">Contact</a>
  </nav>
</header>

<div class="hero" role="img" aria-label="Photo of a dentist examining a smiling patient while an assistant takes notes in a bright clinic"></div>
<div class="appointment-btn">Request An Appointment
  <svg width="18" height="18" viewBox="0 0 18 18"><circle cx="9" cy="9" r="9" fill="#222"/><path d="M7 5l5 4-5 4z" fill="#fff"/></svg>
</div>

<section class="patient-form">
  <h2>Patient’s Form</h2>
  <div class="field" style="left:38px;top:74px;width:137px">First Name</div>
  <div class="field" style="left:197px;top:74px;width:137px">Lastname</div>
  <div class="field" style="left:38px;top:118px;width:137px">Email</div>
  <div class="field" style="left:198px;top:118px;width:137px">Phone No</div>
  <div class="field" style="left:38px;top:161px;width:297px;height:40px;padding-top:13px">How can we help you?</div>
  <div class="submit-btn">Click Here to Get Help Now</div>
</section>

<section class="about">
  <h2>About Ashford Dental</h2>
  <p>Vestibulum rutrum pharetra diam, eget dapibus leo vehicula ut. Fusce aliquam, odio eget adipiscing lobortis.Vestibulum rutrum pharetra diam, eget dapibus leo vehicula ut. Fusce aliquam, odio eget adipiscing lobortis.Vestibulum rutrum pharetra diam, eget dapibus leo vehicula ut. Fusce aliquam, odio eget adipiscing lobortis.Vestibulum rutrum pharetra diam, eget dapibus leo vehicula ut. Fusce aliquam, odio eget adipiscing lobortis.Vestibulum rutrum pharetra diam, eget dapibus leo vehicula ut. Fusce aliquam, odio eget adipiscing lobortis.Vestibulum rutrum pharetra diam, eget dapibus leo vehicula ut. Fusce aliquam, odio eget adipiscing lobortis.Vestibulum rutrum pharetra diam, eget dapibus leo vehicula ut. Fusce aliquam, odio eget adipiscing lobortis.</p>
  <p class="read-more" style="margin-top:10px">[ read More + ]</p>
</section>

<section class="services">
  <div class="service-photo" style="left:115px;top:30px;background:radial-gradient(#f2d6dc,#b98a96)" role="img" aria-label="Illustration of a dental implant in the jaw"></div>
  <div class="service-plus" style="left:170px;top:36px"></div>
  <svg class="abs" style="left:177px;top:43px" width="12" height="12" viewBox="0 0 12 12"><path d="M4.5 1h3v3.5H11v3H7.5V11h-3V7.5H1v-3h3.5z" fill="#c8400f"/></svg>
  <p class="service-text" style="left:210px;top:55px">Vestibulum rutrum pharetra diam, eget dapibus leo vehicula ut. Fusce aliquam, odio eget adipiscing lobortis.Vestibulum lum rutrum pharetra diam, eget</p>
  <p class="read-more abs" style="left:126px;top:138px">[ read More + ]</p>

  <div class="service-photo" style="left:405px;top:30px;background:radial-gradient(#f3ede6,#9a5a4e)" role="img" aria-label="Illustration of a tooth with an implant cross-section"></div>
  <div class="service-plus" style="left:463px;top:36px"></div>
  <svg class="abs" style="left:470px;top:43px" width="12" height="12" viewBox="0 0 12 12"><path d="M4.5 1h3v3.5H11v3H7.5V11h-3V7.5H1v-3h3.5z" fill="#c8400f"/></svg>
  <p class="service-text" style="left:498px;top:55px">Vestibulum rutrum pharetra diam, eget dapibus leo vehicula ut. Fusce aliquam, odio eget adipiscing lobortis.Vestibulum lum rutrum pharetra diam, eget</p>
  <p class="read-more abs" style="left:414px;top:138px">[ read More + ]</p>

  <div class="service-photo" style="left:680px;top:30px;background:radial-gradient(#cfe3f2,#3f7fb8)" role="img" aria-label="Photo of a lab technician working with blue test samples"></div>
  <div class="service-plus" style="left:733px;top:36px"></div>
  <svg class="abs" style="left:740px;top:43px" width="12" height="12" viewBox="0 0 12 12"><path d="M4.5 1h3v3.5H11v3H7.5V11h-3V7.5H1v-3h3.5z" fill="#c8400f"/></svg>
  <p class="service-text" style="left:779px;top:55px">Vestibulum rutrum pharetra diam, eget dapibus leo vehicula ut. Fusce aliquam, odio eget adipiscing lobortis.Vestibulum lum rutrum pharetra diam, eget</p>
  <p class="read-more abs" style="left:694px;top:138px">[ read More + ]</p>
</section>
<div class="skyline" role="img" aria-label="City skyline silhouette"></div>

<footer class="site-footer">
  <div class="footer-brand"><span class="brand-dot"></span><span class="brand-name">Ashford<br>Dental</span></div>
  <div class="contact">Telephone: 03 5550 1284<br>Mobile: 0400 555 219<br>Email: hello@ashforddental.example</div>
  <div class="social"><span></span><span></span><span></span><span></span><span></span></div>
  <div class="newsletter">Sign up to our newsletter</div>
</footer>

</body>
</html>
```